International Trade Consulting Firm Seeks Quality Newsletter Design

Our company provides consulting services to Pinnacle 300 type companies. We compete with the largest consulting companies in the world. However, we have the highest level of expertise in the industry and need to look the most professional and high end. We have very relevant and important information to provide our customers about their compliance and projects. We will have the winning design coded to be an e-newsletter, so it needs to be one page. We want to keep our company colors and logo design in the newsletter, they are attached. We DO NOT want it to look like a mini-version of our website. We want a fresh look to this marketing piece. Newsletter will need to include title, possible sub-heading, space for a feature story, 2 other stories included, and space on either the left or right for short cuts, links or highlights of other articles. Contents/'In this issue' section, about us or branding area, section for relevant links, etc...
Pinnacle 300 companies, High-level management
Marketing

```html
<!DOCTYPE html>
<html lang="en">
<head>
<meta charset="utf-8">
<title>Trade Zone News — Vol. 1</title>
<link href="https://fonts.googleapis.com/css2?family=Arimo:wght@400;700&family=PT+Sans:wght@400;700&display=swap" rel="stylesheet">
<style>
  :root{
    --black:#050505;
    --header-black:#0b0b0b;
    --green-band:#4f8a3a;
    --green-band-light:#6aa24e;
    --forest:#1d3a17;
    --forest-deep:#132a10;
    --column-dark:#162c12;
    --tan:#d8c48b;
    --tan-soft:#e6d7a8;
    --body-text:#e3e6d8;
    --button-green:#1e8f2a;
    --white:#ffffff;
    --rule:#8c927f;
  }
  *{margin:0;padding:0;box-sizing:border-box}
  html,body{width:785px;height:1200px;overflow:hidden;background:var(--black)}
  body{font-family:"PT Sans",Arial,sans-serif;color:var(--body-text)}
  .newsletter{position:relative;width:785px;height:1200px;background:var(--black)}
  .abs{position:absolute}
  h1,h2,h3,h4{font-family:"Arimo",Arial,sans-serif;font-weight:700}

  /* header */
  .masthead{left:0;top:0;width:785px;height:138px;background:linear-gradient(180deg,#000 0%,var(--header-black) 100%)}
  .browser-note{right:33px;top:8px;font-size:11.5px;color:var(--tan-soft)}
  .browser-note a{color:var(--tan-soft)}
  .brand{left:32px;top:26px;width:219px;height:93px;background:#000;display:flex;align-items:center;justify-content:center;gap:8px}
  .brand-mark{width:12px;height:12px;background:var(--tan)}
  .brand-name{font-family:"Arimo",Arial,sans-serif;font-weight:700;font-size:15px;line-height:1.15;color:var(--tan);letter-spacing:.5px}
  .issue-title{right:48px;top:56px;font-size:39px;color:var(--tan)}

  /* band */
  .tagline-band{left:0;top:138px;width:785px;height:50px;background:linear-gradient(180deg,var(--green-band-light),var(--green-band))}
  .tagline{left:41px;top:149px;font-size:26px;color:var(--tan)}
  .volume{right:30px;top:157px;font-family:"Arimo",Arial,sans-serif;font-weight:700;font-size:18px;color:var(--white)}

  /* hero */
  .hero{left:0;top:188px;width:785px;height:283px;background:linear-gradient(135deg,var(--forest-deep) 0%,var(--forest) 60%,#244a1d 100%)}
  .hero-photo{left:38px;top:204px;width:384px;height:255px;background:linear-gradient(160deg,#dfe6ea 0%,#9aa6ad 45%,#3b3a38 80%,#7a4a2e 100%)}
  .article{right:38px;width:290px;text-align:right}
  .article h2{font-size:22px;color:var(--tan);margin-bottom:20px}
  .article p{font-size:10.6px;line-height:14px;text-align:justify;color:var(--body-text)}
  .btn{display:flex;align-items:center;justify-content:center;width:65px;height:15px;background:var(--button-green);border-radius:2px;color:var(--white);font-family:"Arimo",Arial,sans-serif;font-weight:700;font-size:9.5px;text-decoration:none}

  /* section bar */
  .section-bar{left:0;top:471px;width:785px;height:45px;background:var(--black)}
  .section-left{left:38px;top:486px;font-size:19px;color:var(--tan-soft)}
  .section-right{right:40px;top:483px;font-size:20px;color:var(--tan);text-decoration:underline}

  /* columns */
  .col-left{left:0;top:516px;width:413px;height:644px;background:linear-gradient(180deg,#1a3315 0%,var(--column-dark) 100%)}
  .col-right{left:419px;top:516px;width:366px;height:644px;background:linear-gradient(180deg,#1b3416 0%,var(--column-dark) 100%)}

  .contents{left:38px;top:519px;list-style:none}
  .contents li{display:flex;align-items:center;height:25px;font-size:9.6px}
  .contents svg{margin-right:15px}
  .contents a{color:var(--tan-soft)}

  .featured-label{left:38px;top:665px;font-size:20px;color:var(--tan)}
  .featured-art{left:38px;top:693px;width:352px;height:318px;background:linear-gradient(150deg,#f2efe8 0%,#d9d4cc 40%,#b88a62 65%,#2d2f45 100%)}
  .featured-title{left:38px;top:1029px;font-size:23px;color:var(--tan)}
  .featured-text{left:38px;top:1060px;width:350px;font-size:9.8px;line-height:12.6px;text-align:justify}

  .leader-photo{left:453px;top:528px;width:89px;height:97px;border:1px solid var(--tan);background:linear-gradient(180deg,#c9ccce 0%,#b49a84 50%,#2a2a2e 100%)}
  .leader-bio{left:557px;top:530px;width:189px;font-size:8.6px;line-height:11px;text-align:justify}

  .story-label{right:38px;font-size:14px;color:var(--tan-soft)}
  .story-photo{position:absolute}
  .story-link{right:38px;width:150px;text-align:right;font-family:"Arimo",Arial,sans-serif;font-weight:700;font-size:10.3px;line-height:1.15;color:var(--tan);text-decoration:underline}
  .story-text{right:38px;width:154px;font-size:7px;line-height:9.3px;text-align:justify}

  .news-label{right:40px;top:968px;font-size:20px;color:var(--tan);text-decoration:underline}
  .news-item{left:460px;width:288px;font-size:9.8px;line-height:12.5px;color:var(--tan-soft)}
  .news-rule{left:460px;width:286px;border-top:1px dotted var(--rule)}

  .footer{left:0;top:1160px;width:785px;height:40px;background:var(--black);display:flex;align-items:center;justify-content:center;font-size:11.5px;color:var(--tan-soft)}
</style>
</head>
<body>
<div class="newsletter">

  <header>
    <div class="abs masthead"></div>
    <p class="abs browser-note">Is this email not displaying correctly? View it in your <a href="#">browser</a></p>
    <div class="abs brand">
      <span class="brand-mark"></span>
      <span class="brand-name">HARBORLINE TRADE<br>CORPORATION</span>
    </div>
    <h1 class="abs issue-title">Trade Zone News</h1>
  </header>

  <div class="abs tagline-band"></div>
  <h2 class="abs tagline">We have a good news for you!</h2>
  <p class="abs volume">VOL. 1</p>

  <section>
    <div class="abs hero"></div>
    <div class="abs hero-photo" role="img" aria-label="Photo of a business team meeting around a conference table"></div>
    <article class="abs article" style="top:208px">
      <h2>News Article 1</h2>
      <p>Lorem ipsum dolor sit amet, consectetuer adipiscing elit, sed diam nonummy nibh euismod tincidunt ut laoreet dolore magna aliquam erat volutpat. Ut wisi enim ad minim veniam, quis nostrud exerci tation ullamcorper suscipit lobortis nisl ut</p>
    </article>
    <article class="abs article" style="top:333px">
      <h2>News Article 2</h2>
      <p>Lorem ipsum dolor sit amet, consectetuer adipiscing elit, sed diam nonummy nibh euismod tincidunt ut laoreet dolore magna aliquam erat volutpat. Ut wisi enim ad minim veniam, quis nostrud exerci tation ullamcorper suscipit lobortis nisl ut</p>
    </article>
    <a class="abs btn" href="#" style="left:682px;top:438px">READ MORE</a>
  </section>

  <div class="abs section-bar"></div>
  <h3 class="abs section-left">In this Issue</h3>
  <h3 class="abs section-right">LEADER SPEAKS</h3>

  <div class="abs col-left"></div>
  <div class="abs col-right"></div>

  <ul class="abs contents">
    <li><svg width="10" height="10" viewBox="0 0 10 10"><path d="M1 1 L9 5 L1 9 Z" fill="none" stroke="#e6d7a8" stroke-width="1"/></svg><a href="#">Save Money on processing fees</a></li>
    <li><svg width="10" height="10" viewBox="0 0 10 10"><path d="M1 1 L9 5 L1 9 Z" fill="none" stroke="#e6d7a8" stroke-width="1"/></svg><a href="#">Advantages of running a business In a foreign Trade zone</a></li>
    <li><svg width="10" height="10" viewBox="0 0 10 10"><path d="M1 1 L9 5 L1 9 Z" fill="none" stroke="#e6d7a8" stroke-width="1"/></svg><a href="#">Unlock your International Business Possibilities</a></li>
    <li><svg width="10" height="10" viewBox="0 0 10 10"><path d="M1 1 L9 5 L1 9 Z" fill="none" stroke="#e6d7a8" stroke-width="1"/></svg><a href="#">Foreign Trade zone Project Engineering</a></li>
    <li><svg width="10" height="10" viewBox="0 0 10 10"><path d="M1 1 L9 5 L1 9 Z" fill="none" stroke="#e6d7a8" stroke-width="1"/></svg><a href="#">Activations with U.S Customs &amp; Border Protection</a></li>
  </ul>

  <section>
    <h3 class="abs featured-label">Featured Story</h3>
    <div class="abs featured-art" role="img" aria-label="Illustration of a chained shipping crate lifted by a crane hook"></div>
    <h2 class="abs featured-title">Save Money on processing fees</h2>
    <p class="abs featured-text">Lorem ipsum dolor sit amet, consectetuer adipiscing elit, sed diam nonummy nibh euismod tincidunt ut laoreet dolore magna aliquam erat volutpat. Ut wisi enim ad minim veniam, quis nostrud exerci tation ullamcorper suscipit lobortis nisl ut aliquip ex ea commodo consequat. Duis autem vel eum iriure dolor in hendrerit in vulputate velit</p>
    <a class="abs btn" href="#" style="left:325px;top:1141px">READ MORE</a>
  </section>

  <section>
    <div class="abs leader-photo" role="img" aria-label="Portrait photo of the company founder"></div>
    <p class="abs leader-bio">Daniel Marsh is a founder and President of the Harborline Corporation. Mr. Marsh has been involved in the Foreign-Trade Zones Program since 1989 when he began operating and administering Foreign-Trade Zone No. 41 in Riverton, Delmont. This Zone's success set the standard nationwide for Intermodal FTZ Operations, JIT manufacturing Operations and distribution operations. In 1994, along with Evan</p>
    <a class="abs btn" href="#" style="left:680px;top:632px">READ MORE</a>

    <h4 class="abs story-label" style="top:667px">Story 1</h4>
    <div class="story-photo" role="img" aria-label="Photo of two business people shaking hands before a tall window" style="left:452px;top:698px;width:124px;height:83px;background:linear-gradient(180deg,#b9d6ea 0%,#4a7fa8 55%,#0f2c48 100%)"></div>
    <a class="abs story-link" href="#" style="top:698px">Unlock your International Business Possibilities</a>
    <p class="abs story-text" style="top:733px">Lorem ipsum dolor sit amet, consectetuer adipiscing elit, sed diam nonummy nibh euismod tincidunt ut laoreet dolore magna aliquam erat volutpat. Ut wisi enim ad minim veniam, quis</p>

    <h4 class="abs story-label" style="top:802px">Story 2</h4>
    <div class="story-photo" role="img" aria-label="Photo of a person touching a glowing network diagram" style="left:454px;top:828px;width:117px;height:83px;background:radial-gradient(circle at 55% 45%,#8fa3b3 0%,#3c4a56 45%,#101820 100%)"></div>
    <a class="abs story-link" href="#" style="top:829px">Activations with U.S Customs &amp; Border Protection</a>
    <p class="abs story-text" style="top:863px">Lorem ipsum dolor sit amet, consectetuer adipiscing elit, sed diam nonummy nibh euismod tincidunt ut laoreet dolore magna aliquam erat volutpat. Ut wisi enim ad minim veniam, quis</p>
    <a class="abs btn" href="#" style="left:684px;top:933px">READ MORE</a>

    <h3 class="abs news-label">IN THE NEWS</h3>
    <p class="abs news-item" style="top:1004px">Access to Foreign-Trade Zones: Faster and Easier, Thanks to Recent Federal Regulations</p>
    <div class="abs news-rule" style="top:1039px"></div>
    <p class="abs news-item" style="top:1054px">U.S. Foreign-Trade Zones Program Use Grows Among U.S. Based Manufacturing Operations</p>
    <div class="abs news-rule" style="top:1089px"></div>
    <p class="abs news-item" style="top:1104px">Alder Crest LLC Taps into Foreign-Trade Zone Value for Supply Chain, Partners with Harborline Trade Corporation (Harborline Corp)</p>
  </section>

  <footer class="abs footer">Copyright 2014 Harborline Trade Corporation</footer>
</div>
</body>
</html>
```